Moxy Fen needs some awesome stationary

Do you have what it takes to get my brand? You either do or you don't, have a crack at a design and you my just win my business.

I don't want to waste your or my time, so put your creative genius on either a business card or envelope.

I however need a package of stationary that follows the same brand. I will message you to complete the remaining should I like your first submission.

Here is what I need, have a go!

Basically I need the following for my small business based in melbourne.
- Letterhead (printer ready and MS Word)
- Business Card
- Compliments Slip
- Envelope
- Proposal Cover Page (MS Word only)
- Presentation Folder
- Marbled Fox Cards
- Student Name Tent
- Index Cards
- Vell-Ka

I am establishing the brand and it must be modern, professional but also relaxed; that is not formal and not corporate. It represents a company are leaders, but small enough to care and operate like a bunch of friends. We are bringing people and conversations back to business, and turfing out all the bureaucracy and crazy and wasteful procedures. Its about "lets talk and figure it out together and find even better ways".

Target Market(s)

Mainly companies that build software products, but Agile practices are used in many other industries (even graphic design projects)

Industry/Entity Type

Information Technology

Font styles to use
Sans Serif

Colors
3176b5
aaaaaa

Requirements
Must have
• I like curves and circles and not boxes or rectangles.
• I want a colour rich design with my brand colours, but it must be balanced.
• I want more modern than traditional, but simple modern
Should not have
• Not corporate
• Please don't waste my time if your not going to think about it.
• Don't mess with my primary logo
• Don't change my colours
• Don't overlay logo on image

```html
<!DOCTYPE html>
<html lang="en">
<head>
<meta charset="utf-8">
<title>Moxy Fen – Booklet Cover</title>
<link rel="stylesheet" href="https://fonts.googleapis.com/css2?family=Open+Sans:wght@400;600;700&display=swap">
<style>
  :root {
    --brand-blue: #3a5d97;
    --brand-grey: #8b919c;
    --paper-light: #eceef1;
    --paper-mid: #dfe2e6;
    --swirl-soft: #f4f5f7;
    --white: #ffffff;
  }
  * { margin: 0; padding: 0; box-sizing: border-box; }
  html, body {
    width: 1018px;
    height: 1200px;
    overflow: hidden;
    background: var(--paper-mid);
  }
  .cover {
    position: relative;
    width: 1018px;
    height: 1200px;
    font-family: "Open Sans", Arial, sans-serif;
  }
  .cover-art {
    position: absolute;
    inset: 0;
    width: 100%;
    height: 100%;
  }
  .brand {
    position: absolute;
    left: 0;
    right: 0;
    top: 190px;
    display: flex;
    flex-direction: column;
    align-items: center;
    gap: 40px;
  }
  .brand-dot {
    width: 200px;
    height: 200px;
    border-radius: 50%;
    background: var(--brand-blue);
  }
  .brand-name {
    font-size: 86px;
    font-weight: 600;
    line-height: 1;
    color: var(--brand-blue);
    letter-spacing: -0.5px;
  }
  .contact {
    position: absolute;
    left: 0;
    right: 0;
    top: 1010px;
    text-align: center;
    color: var(--white);
  }
  .contact-phone {
    font-size: 70px;
    font-weight: 700;
    line-height: 1;
    letter-spacing: 1px;
  }
  .contact-web {
    margin-top: 22px;
    font-size: 30px;
    font-weight: 400;
    letter-spacing: 3px;
  }
</style>
</head>
<body>
  <main class="cover">
    <svg class="cover-art" viewBox="0 0 1018 1200" aria-hidden="true">
      <defs>
        <linearGradient id="paperShade" x1="0" y1="0" x2="1" y2="1">
          <stop offset="0" stop-color="var(--paper-light)"/>
          <stop offset="1" stop-color="var(--paper-mid)"/>
        </linearGradient>
      </defs>
      <rect class="paper" width="1018" height="1200" fill="url(#paperShade)"/>
      <path class="soft-arc" d="M420 0 C 820 60, 1000 260, 1018 420 L1018 0 Z" fill="var(--swirl-soft)" opacity="0.7"/>
      <path class="soft-arc" d="M0 380 C 160 300, 420 320, 520 460 C 380 380, 160 390, 0 520 Z" fill="var(--swirl-soft)" opacity="0.6"/>
      <path class="grey-swoosh" d="M1018 200 C 1000 560, 780 800, 390 852 C 720 840, 940 760, 1018 600 Z" fill="var(--brand-grey)"/>
      <path class="band-edge" d="M0 650 C 220 880, 760 920, 1018 628 L1018 1200 L0 1200 Z" fill="var(--white)"/>
      <path class="blue-band" d="M0 664 C 220 894, 760 934, 1018 642 L1018 1200 L0 1200 Z" fill="var(--brand-blue)"/>
    </svg>

    <header class="brand">
      <span class="brand-dot" aria-hidden="true"></span>
      <h1 class="brand-name">Moxy Fen</h1>
    </header>

    <footer class="contact">
      <p class="contact-phone">13 000 MOXYF</p>
      <p class="contact-web">www.moxy-fen.com.au</p>
    </footer>
  </main>
</body>
</html>
```